Letter and Envelope Design For Harborline Realty

Please design a letter and an envelope incorporating our logo (See Attached). We are also launched a business card contest. Since we want them to match, please feel free to submit a design for both the business card and also the letter design and envelope.

Requirements
Must have
• The envelope, the letter and the business cards must match somehow connecting the designs. We want them to have something that holds them together besides the logo.

```html
<!DOCTYPE html>
<html lang="en">
<head>
<meta charset="utf-8">
<title>Harborline Realty – Letterhead and Envelopes</title>
<link href="https://fonts.googleapis.com/css2?family=Montserrat:wght@600&family=Questrial&family=Roboto:wght@400&display=swap" rel="stylesheet">
<style>
  :root {
    --backdrop: #dedede;
    --paper: #f7f7f7;
    --navy: #001a8c;
    --slate: #555555;
    --ink: #3c3c3c;
    --ghost: #e6e7ee;
  }
  * { margin: 0; padding: 0; box-sizing: border-box; }
  html, body { width: 1200px; height: 877px; overflow: hidden; background: var(--backdrop); }
  .canvas { position: relative; width: 1200px; height: 877px; }

  .sheet { position: absolute; background: var(--paper); box-shadow: 0 2px 10px rgba(0,0,0,.12); overflow: hidden; }

  .edge-bar { position: absolute; left: 0; top: 0; bottom: 0; }
  .edge-bar .upper { background: var(--slate); }
  .edge-bar .lower { background: var(--navy); }

  .ghost-ring { position: absolute; border: 6px solid var(--ghost); border-radius: 50%; }

  .brand { position: absolute; text-align: center; font-family: "Montserrat", sans-serif; font-weight: 600; color: var(--navy); }
  .brand .ring { display: block; margin: 0 auto; border: 2px solid var(--navy); border-radius: 50%; }
  .brand .name { display: block; letter-spacing: 1.5px; line-height: 1.15; }

  /* Letter */
  .letter { left: 70px; top: 64px; width: 526px; height: 742px; }
  .letter .edge-bar { width: 9px; }
  .letter .edge-bar .upper { height: 172px; }
  .letter .edge-bar .lower { height: 570px; }
  .letter .ghost-ring { left: 106px; top: 216px; width: 312px; height: 312px; }
  .letter .brand { left: 46px; top: 43px; width: 125px; }
  .letter .brand .ring { width: 48px; height: 48px; margin-bottom: 6px; }
  .letter .brand .name { font-size: 12.5px; }
  .letter .brand .name.sub { font-size: 9px; letter-spacing: 3px; }

  .greeting { position: absolute; left: 45px; top: 207px; font-family: "Questrial", sans-serif; font-size: 14px; color: var(--ink); }
  .body-copy { position: absolute; left: 45px; top: 246px; width: 440px; font-family: "Questrial", sans-serif; font-size: 7.6px; line-height: 11.4px; color: var(--ink); text-align: justify; }
  .body-copy p { margin-bottom: 11.4px; }
  .closing { position: absolute; left: 45px; top: 486px; font-family: "Questrial", sans-serif; font-size: 7.6px; color: var(--ink); }
  .signature { position: absolute; left: 40px; top: 520px; width: 94px; height: 38px; background: linear-gradient(90deg, rgba(0,26,140,.12), rgba(0,26,140,.04)); border-radius: 4px; }
  .letter-footer { position: absolute; left: 48px; top: 682px; font-family: "Roboto", sans-serif; font-size: 7.8px; line-height: 13px; color: var(--ink); }

  /* Envelope back */
  .envelope-back { left: 614px; top: 269px; width: 531px; height: 241px; }
  .flap { position: absolute; left: 0; top: 0; }
  .flap-ring { position: absolute; left: 249px; top: 22px; width: 34px; height: 34px; border: 2px solid #fff; border-radius: 50%; }

  /* Envelope front */
  .envelope-front { left: 614px; top: 563px; width: 532px; height: 243px; }
  .envelope-front .edge-bar { width: 10px; }
  .envelope-front .edge-bar .upper { height: 82px; }
  .envelope-front .edge-bar .lower { height: 161px; }
  .envelope-front .ghost-ring { left: 316px; top: 23px; width: 194px; height: 194px; border-width: 4px; }
  .envelope-front .brand { left: 27px; top: 26px; width: 106px; }
  .envelope-front .brand .ring { width: 38px; height: 38px; margin-bottom: 5px; }
  .envelope-front .brand .name { font-size: 10.5px; }
  .envelope-front .brand .name.sub { font-size: 7.5px; letter-spacing: 2.5px; }
  .return-address { position: absolute; left: 27px; top: 94px; width: 106px; text-align: center; font-family: "Roboto", sans-serif; font-size: 8px; line-height: 10px; color: var(--ink); }
</style>
</head>
<body>
<div class="canvas">

  <section class="sheet letter">
    <div class="edge-bar"><div class="upper"></div><div class="lower"></div></div>
    <div class="ghost-ring"></div>
    <div class="brand">
      <span class="ring"></span>
      <span class="name">HARBORLINE</span>
      <span class="name sub">REALTY</span>
    </div>
    <p class="greeting">Dear Mr. Carter,</p>
    <div class="body-copy">
      <p>Lorem ipsum dolor sit amet, consectetur adipiscing elit. Donec orci purus, luctus vitae dignissim eu, iaculis sed purus. Vivamus faucibus, ipsum nec aliquet viverra, leo mauris condimentum ligula, sit amet sagittis enim ligula quis arcu. Nam egestas tortor id nisi porttitor mattis. In tortor ante, ultricies in suscipit a, tempus non massa. Vivamus et auctor mi. Fusce vel massa nulla. Phasellus nec eros mauris, et scelerisque orci.</p>
      <p>Donec malesuada orci vitae nulla accumsan porta a id massa. Quisque accumsan iaculis magna sit amet fringilla. Maecenas consequat, magna eget tincidunt semper, odio nibh rutrum mi, id feugiat ante nisi eu risus. Vestibulum nunc orci, rhoncus a placerat in, ultricies in mi. Cras mattis varius eros, vel fringilla nisi suscipit eget. Quisque scelerisque sagittis nulla at porttitor.</p>
      <p>Sed id augue vitae urna euismod commodo aliquet a quam. Pellentesque arcu velit, cursus et malesuada ut, consequat et diam. Nullam erat sem, rhoncus id ullamcorper vitae, rhoncus et arcu. In ultricies ultricies nulla, ut rutrum nisi iaculis at. Donec eu magna a metus ornare faucibus. Fusce aliquet faucibus ultricies. Morbi semper, est id tincidunt gravida, sem arcu adipiscing lacus, ac bibendum nulla leo eu purus. Quisque nec diam sed risus consectetur a ccumsan quis quis nibh. Vestibulum id purus lorem.</p>
      <p>It is a long established fact that a reader will be distracted by the readable content of a page when looking at its layout. The point of using Lorem Ipsum is that it has a more-or-less normal distribution of letters, as opposed to using 'Content here, content here', making it look like readable English. Many desktop publishing packages</p>
    </div>
    <p class="closing">Sincerely,</p>
    <div class="signature" role="img" aria-label="Handwritten signature of Daniel Reyes"></div>
    <div class="letter-footer">
      4120 Juniper Lane, Anchorage, Alaska 34512<br>
      P. 555 210 4417 F. 555 210 4418 E. hello@harborline.example W. www.harborline.example
    </div>
  </section>

  <section class="sheet envelope-back">
    <svg class="flap" width="531" height="74" viewBox="0 0 531 74">
      <path d="M0 0 H531 L521 42 Q514 74 484 74 H47 Q17 74 10 42 Z" fill="var(--navy)"/>
    </svg>
    <div class="flap-ring"></div>
  </section>

  <section class="sheet envelope-front">
    <div class="edge-bar"><div class="upper"></div><div class="lower"></div></div>
    <div class="ghost-ring"></div>
    <div class="brand">
      <span class="ring"></span>
      <span class="name">HARBORLINE</span>
      <span class="name sub">REALTY</span>
    </div>
    <p class="return-address">4120 Juniper Lane<br>Anchorage, Alaska 34512</p>
  </section>

</div>
</body>
</html>
```